Transform Your Giving

I need a tri-fold brochure that will fit in a standard number 10 business envelope. Meadowlark and Allied Services is a charitable nonprofit. The goal of this brochure is to stimulate people into thinking about other ways to make a donation. The design should communicate the essential information on donation options, create a sense of professional integrity, be graphically sharp, easy to read and laid out in a way that doesn't make the material appear crowded.

```html
<!DOCTYPE html>
<html lang="en">
<head>
<meta charset="utf-8">
<title>Transform Your Giving - Meadowlark and Allied Services</title>
<link href="https://fonts.googleapis.com/css2?family=Barlow:ital,wght@0,400;0,500;0,600;0,700;1,600;1,700&display=swap" rel="stylesheet">
<style>
:root{
  --stage:#7a7a7a;
  --navy:#2b2577;
  --navy-deep:#241f66;
  --green:#3db34a;
  --ink:#2e2e38;
  --white:#ffffff;
  --photo-warm:#d9cfc4;
  --photo-soft:#e8e4e0;
  --photo-park:#6f8f4f;
}
*{box-sizing:border-box;margin:0;padding:0}
html,body{width:1096px;height:1200px;overflow:hidden}
body{background:var(--stage);font-family:"Barlow",Arial,sans-serif;color:var(--ink);position:relative}
.sheet{position:absolute;left:205px;width:687px;height:515px;display:flex}
.sheet--outside{top:63px}
.sheet--inside{top:621px}
.panel{width:229px;height:515px;position:relative;overflow:hidden;background:var(--white)}
.panel--navy{background:var(--navy);color:var(--white)}
.photo{position:absolute;left:0;width:229px}
.arc{position:absolute;left:0;width:229px;height:34px;display:block}
.icon-symbols{position:absolute;width:0;height:0}

/* icon badges */
.badge{border-radius:50%;background:var(--navy);display:flex;align-items:center;justify-content:center;flex-shrink:0;box-shadow:0 0 0 2px var(--white),0 0 0 3.5px var(--navy)}
.badge svg{width:58%;height:58%}
.badge--ring{box-shadow:0 0 0 3px var(--white),0 0 0 5px var(--green)}
.badge--green{background:var(--green);box-shadow:0 0 0 3px var(--navy),0 0 0 5px var(--green)}

/* panel A */
.impact{position:absolute;left:18px;top:218px;width:200px}
.impact h2{font-size:13px;font-weight:700;color:var(--navy);letter-spacing:.1px;line-height:1.1}
.impact p{font-size:10px;line-height:12.9px;font-weight:500;margin-top:2px}
.option-grid{position:absolute;left:18px;top:352px;width:200px;height:145px}
.option{position:absolute;display:flex;align-items:center;gap:6px;font-size:10.5px;font-weight:600;color:var(--ink);line-height:13px}
.option .badge{width:40px;height:40px}
.connector{position:absolute;border-left:1.5px dotted var(--navy);width:0}
.name-mark{font-weight:700;color:var(--navy);text-align:center;line-height:1}
.name-mark--faint{position:absolute;right:18px;bottom:16px;color:#b9b9c0;font-size:18px;width:90px}
.name-mark small{display:block;font-size:5px;font-weight:600;letter-spacing:.3px;margin-top:2px}

/* panel B */
.panel-b{text-align:center}
.panel-b .lead{position:absolute;left:14px;right:14px;top:18px;font-size:9px;line-height:11.5px;font-weight:500}
.panel-b .quote{position:absolute;left:14px;right:14px;top:97px;font-size:8.8px;line-height:11.5px;font-weight:400}
.panel-b .will{position:absolute;left:10px;right:10px;top:201px;font-size:8.6px;line-height:11px;font-weight:500}
.panel-b .will a{color:var(--green);text-decoration:underline}
.glow{position:absolute;left:0;top:60px;width:229px;height:130px;background:radial-gradient(ellipse at 70% 50%,rgba(90,80,190,.55),rgba(43,37,119,0) 70%)}
.name-mark--light{position:absolute;left:0;right:0;top:254px;color:var(--white);font-size:30px;display:flex;align-items:center;justify-content:center;gap:6px}
.name-mark--light .dot{width:10px;height:10px;border-radius:50%;background:var(--green)}
.name-mark__sub{position:absolute;left:0;right:0;top:309px;font-size:5.6px;font-weight:700;letter-spacing:.4px;color:var(--white)}
.contact{position:absolute;left:10px;right:10px;top:330px}
.contact h3{font-size:10.5px;font-weight:700;text-decoration:underline}
.contact .ask{color:var(--green);font-size:8.8px;font-weight:600;line-height:11.5px;margin-top:6px}
.contact-item{font-size:8.3px;line-height:10.5px;letter-spacing:.2px;margin-top:3px}
.contact-item .ico{display:block;width:8px;height:8px;margin:0 auto 2px}
.follow{margin-top:6px;font-size:9px;font-weight:700;display:flex;align-items:center;justify-content:center;gap:3px}
.follow span.u{text-decoration:underline;margin-right:2px}
.follow .social{width:9px;height:9px;border-radius:50%;background:var(--green)}

/* panel C */
.cover-title{position:absolute;left:0;right:0;top:14px;text-align:center}
.cover-title h1{font-size:17.5px;font-weight:700;color:var(--navy);line-height:20px}
.cover-title .strap{font-size:17.5px;font-weight:700;color:var(--green);line-height:20px}
.cover-title p{font-size:8.8px;font-weight:700;color:var(--navy);line-height:11px;margin-top:5px}
.cover-icons{position:absolute;left:0;top:290px;width:229px;height:132px}
.cover-icon{position:absolute;width:70px;text-align:center;font-size:10.5px;font-weight:700;color:var(--ink);line-height:13px}
.cover-icon .badge{width:40px;height:40px;margin:0 auto 4px}
.hline{position:absolute;border-top:1.5px dotted var(--navy);height:0}
.name-mark--cover{position:absolute;left:0;right:0;top:436px;font-size:34px;display:flex;align-items:center;justify-content:center;gap:6px}
.name-mark--cover .dot{width:11px;height:11px;border-radius:50%;background:var(--green)}
.cover-sub{position:absolute;left:0;right:0;top:492px;text-align:center;font-size:6.2px;font-weight:700;color:var(--navy);letter-spacing:.4px}

/* inside panels */
.inside{padding:16px 13px 0 18px}
.intro{font-size:8.9px;line-height:11.5px;font-weight:500}
.strategy{display:flex;gap:8px;align-items:flex-start;margin-top:8px}
.strategy .badge{width:48px;height:48px;margin-top:2px}
.strategy h3{font-size:9.6px;font-weight:700;color:var(--navy);line-height:11.5px}
.strategy .tag{font-size:8.6px;font-weight:700;font-style:italic;color:var(--green);line-height:11px;margin-top:2px}
.body{font-size:8.2px;line-height:10.6px;margin-top:3px}
.how{font-size:10.5px;font-weight:700;color:var(--navy);margin-top:7px;line-height:12px}
.panel--navy .strategy h3{color:var(--white)}
.panel--navy .how{color:var(--green)}
.panel--navy .body{color:var(--white)}
.ticks{list-style:none;margin-top:6px}
.ticks li{font-size:7.9px;line-height:10.3px;padding-left:10px;position:relative;margin-bottom:5px}
.ticks li svg{position:absolute;left:0;top:2px;width:7px;height:7px}
</style>
</head>
<body>

<svg class="icon-symbols" aria-hidden="true">
  <defs>
    <symbol id="i-coin" viewBox="0 0 24 24"><g fill="none" stroke="#fff" stroke-width="1.6"><circle cx="12" cy="12" r="9"/><path d="M9 7v10M9 7h4a2.5 2.5 0 0 1 0 5H9m0 0h4.5a2.5 2.5 0 0 1 0 5H9"/></g></symbol>
    <symbol id="i-bank" viewBox="0 0 24 24"><g fill="none" stroke="#fff" stroke-width="1.4"><path d="M3 9 12 4l9 5z"/><path d="M3 9h18M5 10v8M9 10v8M15 10v8M19 10v8M3 19h18M2 21h20"/></g></symbol>
    <symbol id="i-gift" viewBox="0 0 24 24"><g fill="none" stroke="#fff" stroke-width="1.4"><rect x="3" y="9" width="18" height="4"/><rect x="5" y="13" width="14" height="8"/><path d="M12 9v12M12 9c-2-4-6-4-5-1s5 1 5 1c2-4 6-4 5-1s-5 1-5 1"/></g></symbol>
    <symbol id="i-chart" viewBox="0 0 24 24"><g fill="none" stroke="#fff" stroke-width="1.4"><rect x="4" y="15" width="3" height="5"/><rect x="10" y="12" width="3" height="8"/><rect x="16" y="9" width="3" height="11"/><path d="M3 12 9 7l3 3 7-6M15 4h4v4"/><path d="M2 21h20"/></g></symbol>
    <symbol id="i-annuity" viewBox="0 0 24 24"><g fill="none" stroke="#fff" stroke-width="1.3"><rect x="3" y="6" width="18" height="15" rx="1"/><path d="M3 10h18M7 4v4M17 4v4"/><circle cx="12" cy="8" r="3.2"/><path d="M12 6.3v3.4"/><path d="M6 13h2M11 13h2M16 13h2M6 17h2M11 17h2M16 17h2"/></g></symbol>
    <symbol id="i-tick" viewBox="0 0 10 10"><circle cx="5" cy="5" r="5" fill="#2b2577"/><path d="M2.8 5.2 4.4 6.7 7.3 3.5" fill="none" stroke="#fff" stroke-width="1.3"/></symbol>
  </defs>
</svg>

<!-- Outside of the brochure -->
<section class="sheet sheet--outside">

  <article class="panel panel-a">
    <div class="photo" style="top:0;height:216px;background:linear-gradient(160deg,var(--photo-soft),var(--photo-warm) 60%,#8d8aa8)" role="img" aria-label="Photo of an older man and a young woman smiling at a laptop"></div>
    <svg class="arc" style="top:186px" viewBox="0 0 229 34" preserveAspectRatio="none"><path d="M0 34V28Q114.5 -8 229 28V34Z" fill="#fff"/><path d="M0 28Q114.5 -8 229 28" fill="none" stroke="#3db34a" stroke-width="3"/></svg>
    <div class="impact">
      <h2>THE IMPACT OF YOUR GIFT</h2>
      <p>Your generosity drives our mission. With every Smart gift you're supporting Meadowlark and Allied Services. Join our community of Smart Givers today and make an enduring impact. With Smart Giving your generosity reaches further. Begin your Smart Giving journey with us today.</p>
    </div>
    <div class="option-grid">
      <div class="connector" style="left:20px;top:40px;height:12px"></div>
      <div class="connector" style="left:20px;top:92px;height:10px"></div>
      <div class="connector" style="left:112px;top:40px;height:12px"></div>
      <div class="option" style="left:0;top:0"><span class="badge"><svg><use href="#i-coin"/></svg></span>Crypto</div>
      <div class="option" style="left:92px;top:0"><span class="badge"><svg><use href="#i-chart"/></svg></span>Stocks &amp;<br>Securities</div>
      <div class="option" style="left:0;top:51px"><span class="badge"><svg><use href="#i-bank"/></svg></span>DAF's</div>
      <div class="option" style="left:92px;top:51px"><span class="badge"><svg><use href="#i-annuity"/></svg></span>Charitable<br>Annuity</div>
      <div class="option" style="left:0;top:101px"><span class="badge"><svg><use href="#i-gift"/></svg></span>QCDs</div>
    </div>
    <div class="name-mark name-mark--faint">MAAS<small>MEADOWLARK AND ALLIED SERVICES</small></div>
  </article>

  <article class="panel panel--navy panel-b">
    <div class="glow" role="img" aria-label="Faint photo of joined hands in navy tones"></div>
    <p class="lead">To learn more about Smart Giving Options and how they can benefit you and Meadowlark and Allied Services, please reach out to our team. We're here to help you navigate these giving methods and answer any question you may have.</p>
    <p class="quote">Being kind to others is a way of<br>being good to yourself.<br>Miriam Ashby</p>
    <p class="will">If you do not have a will, go to<br><a href="#">www.simplewillhub.org</a><br>In 20 minutes you can have a legal will &ndash; for free.</p>
    <div class="name-mark name-mark--light"><span class="dot"></span>MAAS</div>
    <div class="name-mark__sub">MEADOWLARK AND ALLIED SERVICES, INC.</div>
    <div class="contact">
      <h3>CONTACT US</h3>
      <p class="ask">Have more question? Please contact us at<br>Meadowlark and Allied Services</p>
      <p class="contact-item"><svg class="ico" viewBox="0 0 10 10"><circle cx="5" cy="5" r="5" fill="#3db34a"/><path d="M5 2.2a2 2 0 0 0-2 2c0 1.5 2 3.6 2 3.6s2-2.1 2-3.6a2 2 0 0 0-2-2z" fill="#fff"/></svg>1420 Prairie View Rd.<br>Suite 2 Fairhaven, ND 58000</p>
      <p class="contact-item"><svg class="ico" viewBox="0 0 10 10"><circle cx="5" cy="5" r="5" fill="#3db34a"/><path d="M3 2.6 4.2 3.8 3.6 4.6a4 4 0 0 0 1.8 1.8l.8-.6L7.4 7 6.6 7.8A5 5 0 0 1 2.2 3.4z" fill="#fff"/></svg>555-014-2200 (ext. 100)</p>
      <p class="contact-item"><svg class="ico" viewBox="0 0 10 10"><circle cx="5" cy="5" r="5" fill="#3db34a"/><rect x="2.6" y="3.3" width="4.8" height="3.4" fill="#fff"/><path d="M2.6 3.3 5 5.2l2.4-1.9" fill="none" stroke="#3db34a" stroke-width=".6"/></svg>info@meadowlarkallied.org</p>
      <p class="contact-item"><svg class="ico" viewBox="0 0 10 10"><circle cx="5" cy="5" r="5" fill="#3db34a"/><circle cx="5" cy="5" r="2.6" fill="none" stroke="#fff" stroke-width=".7"/><path d="M2.4 5h5.2M5 2.4v5.2" stroke="#fff" stroke-width=".6"/></svg>www.meadowlarkallied.org</p>
      <p class="follow"><span class="u">FOLLOW US:</span><span class="social"></span><span class="social"></span></p>
    </div>
  </article>

  <article class="panel panel-c">
    <header class="cover-title">
      <h1>Transform Your Giving</h1>
      <div class="strap">Be Strategic, Be Smart</div>
      <p>Discover the impact of Smart Giving with<br>Meadowlark and Allied Services</p>
    </header>
    <div class="photo" style="top:92px;height:200px;background:linear-gradient(170deg,#f2efec,var(--photo-soft) 40%,#d8cdc4)" role="img" aria-label="Photo of a smiling older couple embracing"></div>
    <svg class="arc" style="top:88px" viewBox="0 0 229 34" preserveAspectRatio="none"><path d="M0 0H229V28Q114.5 -8 0 28Z" fill="#fff"/><path d="M0 28Q114.5 -8 229 28" fill="none" stroke="#3db34a" stroke-width="3"/></svg>
    <svg class="arc" style="top:264px" viewBox="0 0 229 34" preserveAspectRatio="none"><path d="M0 34V28Q114.5 -8 229 28V34Z" fill="#fff"/><path d="M0 28Q114.5 -8 229 28" fill="none" stroke="#3db34a" stroke-width="3"/></svg>
    <div class="cover-icons">
      <div class="hline" style="left:58px;top:21px;width:42px"></div>
      <div class="hline" style="left:129px;top:21px;width:42px"></div>
      <div class="hline" style="left:94px;top:82px;width:42px"></div>
      <div class="cover-icon" style="left:9px;top:1px"><span class="badge"><svg><use href="#i-coin"/></svg></span>CRYPTO</div>
      <div class="cover-icon" style="left:80px;top:1px"><span class="badge"><svg><use href="#i-bank"/></svg></span>DAF'S</div>
      <div class="cover-icon" style="left:150px;top:1px"><span class="badge"><svg><use href="#i-gift"/></svg></span>QCDS</div>
      <div class="cover-icon" style="left:45px;top:62px"><span class="badge"><svg><use href="#i-chart"/></svg></span>STOCKS &amp;<br>SECURITIES</div>
      <div class="cover-icon" style="left:114px;top:62px"><span class="badge"><svg><use href="#i-annuity"/></svg></span>CHARITABLE<br>ANNUITY</div>
    </div>
    <div class="name-mark name-mark--cover"><span class="dot"></span>MAAS</div>
    <div class="cover-sub">MEADOWLARK AND ALLIED SERVICES, INC.</div>
  </article>
</section>

<!-- Inside of the brochure -->
<section class="sheet sheet--inside">

  <article class="panel inside">
    <p class="intro">We would like to introduce you to five Strategic and Smart ways to give that could potentially be more beneficial to you compared to traditional cash donations. We encourage you to keep this information as a guide for your future contributions.</p>
    <div class="strategy">
      <span class="badge badge--ring"><svg><use href="#i-chart"/></svg></span>
      <div><h3>Gifts of Stocks or Appreciated Assets Strategic &amp; Smart</h3><p class="tag">Consider your long-term publicly traded stock as a way to give to your favorite charity.</p></div>
    </div>
    <p class="body">You can make a significantly bigger impact when you donate long-term appreciated securities, including stock, mutual funds, &amp; bonds, directly to your favorite charity.</p>
    <h4 class="how">How Does It Work?</h4>
    <p class="body" style="margin-top:1px">When you donate stock to a charity, you will generally take a tax deduction for the full market value. Because you are donating stock, your contribution &amp; tax deduction may be significantly higher than contributing the after-tax proceeds. The same benefits apply when you donate mutual funds or bonds.</p>
    <div class="strategy" style="margin-top:14px">
      <span class="badge badge--ring"><svg><use href="#i-bank"/></svg></span>
      <div><h3>Donor-Advised Fund (DAF)<br>Strategic &amp; Smart</h3><p class="tag">Consider a DAF &ndash; a simple, flexible, and tax-advantageous way to give to your favorite charities.</p></div>
    </div>
    <p class="body">A Donor-Advised Fund (DAF), is like a charitable investment account for the sole purpose of supporting your favorite charities.</p>
    <h4 class="how">How Does It Work?</h4>
    <p class="body" style="margin-top:1px">You establish a DAF &amp; contribute cash, stocks, or non-publicly traded assets, cryptocurrency, &amp; private company stock to be eligible for an immediate tax deduction. Those funds are contributed for tax-free growth. You can recommend grants be made from your DAF to any IRS qualified public charity.</p>
  </article>

  <article class="panel panel--navy inside">
    <div class="strategy" style="margin-top:2px">
      <span class="badge badge--green"><svg><use href="#i-gift"/></svg></span>
      <div><h3>Qualified Charitable Distributions (QCDs) Strategic &amp; Smart</h3><p class="tag">Consider a QCD &ndash; when planning your IRA withdrawal strategy... &amp; donate to your favorite charity.</p></div>
    </div>
    <p class="body">IRA owners at age 70 &frac12; or over can transfer dollars from their IRA to charity tax-free each year. These transfers known as Qualified Charitable Distributions (QCDs) offer eligible older Americans a great way to easily give to charity.</p>
    <h4 class="how">How Does It Work?</h4>
    <p class="body" style="margin-top:1px">Are you 72 and required to take a minimum distribution (RMD) from your IRA but do not need the funds? Consider a Qualified Charitable Distribution. Normally, distributions from a traditional IRA are taxable when received. With a QCD, these distributions become tax-free when paid directly from the IRA to your favorite eligible charity. An IRA owner wishing to make a QCD should contact their IRA trustee, allowing time to complete the transaction before the end of the year to receive the tax benefit.</p>
    <div class="strategy" style="margin-top:18px">
      <span class="badge badge--green"><svg><use href="#i-annuity"/></svg></span>
      <div><h3>Charitable Gift Annuity<br>Strategic &amp; Smart</h3><p class="tag">Consider establishing a<br>Charitable Gift Annuity</p></div>
    </div>
    <p class="body" style="margin-top:7px">You make a donation to a single charity. The gift is set aside in a reserve account and invested.</p>
    <h4 class="how" style="margin-top:5px">How Does It Work?</h4>
    <p class="body" style="margin-top:1px">A charitable gift annuity is a contract between a donor &amp; a charity. As a donor, you make a sizable gift to charity using cash, securities, or possibly other assets. This money is then invested. In return, you become eligible to take a partial tax deduction for your donation, plus you receive a fixed stream of income from the charity for the rest of your life. At the end of your life (as well as your spouse's, if you're giving as a couple), the charity receives the remainder of the gift.</p>
  </article>

  <article class="panel inside" style="padding-left:17px">
    <div class="strategy" style="margin-top:2px">
      <span class="badge badge--ring"><svg><use href="#i-coin"/></svg></span>
      <div><h3>Cryptocurrency<br>Strategic &amp; Smart</h3><p class="tag">Consider donating Bitcoin and other cryptocurrencies to your favorite charity.</p></div>
    </div>
    <p class="body" style="font-size:8.9px;line-height:11.8px;margin-top:6px">Bitcoin and other cryptocurrencies can be donated to charity just like other appreciated assets such as stocks and other business interests. Before you sell bitcoin &amp; donate the after-tax proceeds, consider donating your bitcoin directly to a favorite charity.</p>
    <h4 class="how" style="margin-top:9px">How Does It Work?</h4>
    <p class="body" style="margin-top:1px">Many donors find it useful to open a Donor-Advised Fund (DAF). This strategy includes two significant benefits, both for you and your favorite charity.</p>
    <ul class="ticks">
      <li><svg><use href="#i-tick"/></svg>Your tax deduction will be equal to the fair market value of the donated bitcoin (as determined by a qualified appraisal).</li>
      <li><svg><use href="#i-tick"/></svg>Your cryptocurrency donation is tax-smart because it may eliminate capital gains taxes on the value / appreciation AND your favorite charity will receive 100% of the value of the contribution.</li>
    </ul>
    <p class="body" style="margin-top:2px">Often charities are not able to accept direct donations of bitcoin/crypto so using a DAF is a great way to donate these assets.</p>
    <div class="photo" style="top:370px;height:145px;background:linear-gradient(180deg,#9bb66f,var(--photo-park) 55%,#7d6a4f)" role="img" aria-label="Photo of an older couple sharing gift bags on a park bench"></div>
    <svg class="arc" style="top:364px" viewBox="0 0 229 34" preserveAspectRatio="none"><path d="M0 0H229V28Q114.5 -8 0 28Z" fill="#fff"/><path d="M0 28Q114.5 -8 229 28" fill="none" stroke="#3db34a" stroke-width="3"/></svg>
  </article>
</section>

</body>
</html>
```